Tech business card design

We need an amazing business card design for our new business 'Pexla' a marketing tech startup based in Sydney, Australia. We provide an online marketplace for businesses to search and buy advertising media, connect with service providers and learn more about marketing. We wish to communicate 'cool tech', reliability and professionalism and design based around our logo.

Target Market(s)

Business Owners

Contact Information for Business Card

Name
Position
Email Address
Website
Phone Number

Font styles to use
Other font styles liked:
• Avenir & Avenir Next

Colors

Designer to choose colors to be used in the design.

```html
<!DOCTYPE html>
<html lang="en">
<head>
<meta charset="utf-8">
<title>Pexla business card</title>
<link rel="stylesheet" href="https://fonts.googleapis.com/css2?family=Mulish:wght@400;600;800&display=swap">
<style>
  :root {
    --stage: #3a3a3c;
    --navy: #14164a;
    --navy-deep: #0a0b22;
    --tech-blue: #2a2fa0;
    --card-light: #e6e6e8;
    --ink: #1b1b22;
    --muted: #55555c;
    --white: #ffffff;
  }
  * { margin: 0; padding: 0; box-sizing: border-box; }
  html, body { width: 1200px; height: 1000px; overflow: hidden; }
  body {
    background: radial-gradient(ellipse at 50% 40%, #4a4a4d 0%, var(--stage) 70%);
    font-family: "Mulish", "Avenir Next", Arial, sans-serif;
    position: relative;
  }
  .card {
    position: absolute;
    width: 720px;
    height: 410px;
    border-radius: 26px;
    overflow: hidden;
    box-shadow: 0 18px 40px rgba(0,0,0,0.45);
  }
  /* back of card */
  .card-back { left: 380px; top: 60px; background: var(--navy-deep); }
  .card-back .tech-art {
    position: absolute; inset: 0;
    background: radial-gradient(ellipse at 50% 50%, var(--tech-blue) 0%, #151763 35%, var(--navy-deep) 80%);
  }
  .card-back .brand-name {
    position: absolute; left: 0; right: 0; top: 50%;
    transform: translateY(-50%);
    text-align: center;
    color: var(--white);
    font-weight: 800;
    font-size: 120px;
    letter-spacing: -2px;
    line-height: 1;
  }
  /* front of card */
  .card-front { left: 100px; top: 520px; background: var(--card-light); }
  .card-front .brand-name {
    position: absolute; left: 58px; top: 120px;
    color: var(--navy);
    font-weight: 800;
    font-size: 84px;
    letter-spacing: -2px;
    line-height: 1;
  }
  .card-front .divider {
    position: absolute; left: 318px; top: 108px;
    width: 2px; height: 150px; background: var(--ink);
  }
  .contact-block { position: absolute; left: 345px; top: 112px; color: var(--ink); }
  .person-name { font-size: 25px; font-weight: 600; line-height: 1.1; }
  .person-role { font-size: 15px; color: var(--muted); margin-bottom: 18px; }
  .contact-line { display: flex; align-items: center; gap: 9px; font-size: 16px; margin-bottom: 6px; }
  .contact-line svg { width: 22px; height: 22px; flex: none; }
  .wave { position: absolute; left: 0; bottom: 0; width: 720px; height: 170px; }
</style>
</head>
<body>
  <section class="card card-back">
    <div class="tech-art" role="img" aria-label="Abstract blue technology circuitry background"></div>
    <div class="brand-name">Pexla</div>
  </section>

  <section class="card card-front">
    <svg class="wave" viewBox="0 0 720 170" preserveAspectRatio="none" aria-hidden="true">
      <path d="M0 0 C120 -10 220 40 330 90 C450 145 580 130 720 105 L720 170 L0 170 Z" fill="var(--navy)"/>
      <path d="M0 8 C130 0 230 50 340 100 C460 150 590 138 720 118" fill="none" stroke="var(--white)" stroke-width="2"/>
    </svg>
    <div class="brand-name">Pexla</div>
    <div class="divider"></div>
    <div class="contact-block">
      <div class="person-name">Marcus Lane</div>
      <div class="person-role">Managing Director</div>
      <div class="contact-line">
        <svg viewBox="0 0 22 22" aria-hidden="true"><circle cx="11" cy="11" r="10" fill="none" stroke="var(--ink)" stroke-width="1.4"/><rect x="7.5" y="5" width="7" height="12" rx="1.2" fill="none" stroke="var(--ink)" stroke-width="1.3"/></svg>
        <span>800-214-5573</span>
      </div>
      <div class="contact-line">
        <svg viewBox="0 0 22 22" aria-hidden="true"><circle cx="11" cy="11" r="10" fill="none" stroke="var(--ink)" stroke-width="1.4"/><rect x="6" y="7.5" width="10" height="7" fill="none" stroke="var(--ink)" stroke-width="1.3"/><path d="M6 7.5 L11 11.5 L16 7.5" fill="none" stroke="var(--ink)" stroke-width="1.2"/></svg>
        <span>marcusl@pexlamail.com</span>
      </div>
      <div class="contact-line">
        <svg viewBox="0 0 22 22" aria-hidden="true"><circle cx="11" cy="11" r="10" fill="var(--ink)"/><circle cx="11" cy="11" r="6" fill="none" stroke="var(--white)" stroke-width="1.1"/><ellipse cx="11" cy="11" rx="2.6" ry="6" fill="none" stroke="var(--white)" stroke-width="1"/><path d="M5 11 H17" stroke="var(--white)" stroke-width="1"/></svg>
        <span>www.pexla.com</span>
      </div>
    </div>
  </section>
</body>
</html>
```